Business Card Design For Office Furniture Clearance Company

Kestrel Office Clearance - our company name pretty much explains what we do, we clear offices for high end clients, mainly plc's and large international companies.

We require a nice looking business card that displays professionalism but without being too serious.

It would be nice to see just a little more than a conventional boring business card, make sure you add some flare.

Industry/Entity Type

Office Furniture

Contact Information for Business Card

CARD 1

Mark Holloway
Director
mark@kestrelofficeclearance.co.uk
m: 07700 153928

t: 01632 960418
www.kestrelofficeclearance.co.uk

Kestrel Office Clearance
Unit K4 B
2-8 Fenwick Lane
Kelmsdown
Brackenford
ZZ9 4QT

free office clearances… you cant get better than that.

CARD 2

Peter Radford
Director
peter@kestrelofficeclearance.co.uk
m: 07700 382615

t: 01632 960418

Kestrel Office Clearance
Unit K4 B
2-8 Fenwick Lane
Kelmsdown
Brackenford
ZZ9 4QT

Font styles to use
Sans Serif

Requirements
Must have
• A white background - as we have a blue logo.
Nice to have
• Nice use of the logo - play around with this and dissect it.

```html
<!DOCTYPE html>
<html lang="en">
<head>
<meta charset="utf-8">
<title>Kestrel Office Clearance – Business Card</title>
<link rel="stylesheet" href="https://fonts.googleapis.com/css2?family=Montserrat:wght@500;600;700&display=swap">
<style>
  :root {
    --ink: #050505;
    --paper: #ffffff;
    --brand-blue: #1f6aa5;
    --flame-dark: #1c1c1c;
    --flame-mid: #2e2e2e;
    --backdrop: #e6e7ea;
  }
  * { box-sizing: border-box; margin: 0; padding: 0; }
  html, body {
    width: 1200px; height: 900px; overflow: hidden;
    background: var(--backdrop);
    font-family: "Montserrat", sans-serif;
  }
  .sheet {
    position: relative; width: 1200px; height: 900px;
    display: flex; flex-direction: column; align-items: center; justify-content: center; gap: 40px;
  }
  .card {
    position: relative; width: 640px; height: 390px;
    border-radius: 22px; overflow: hidden;
    background: var(--ink);
    box-shadow: 0 10px 28px rgba(0,0,0,.25);
  }

  /* Front */
  .card-front .flame-area {
    position: absolute; left: 0; bottom: 0; width: 230px; height: 300px;
    background: radial-gradient(ellipse at 40% 70%, var(--flame-mid) 0%, var(--flame-dark) 55%, rgba(5,5,5,0) 80%);
  }
  .card-front .brand {
    position: absolute; left: 200px; top: 110px;
    display: flex; align-items: center; gap: 18px;
  }
  .brand-dot {
    width: 70px; height: 70px; border-radius: 50%; background: var(--brand-blue); flex: none;
  }
  .brand-name {
    color: var(--paper); font-weight: 700; font-size: 30px; line-height: 1.1; letter-spacing: .5px;
  }
  .card-front .web {
    position: absolute; left: 268px; top: 232px;
    color: var(--paper); font-size: 13px; font-weight: 600; letter-spacing: .8px;
  }
  .card-front .tagline {
    position: absolute; left: 30px; right: 30px; bottom: 34px;
    color: var(--paper); font-size: 16px; font-weight: 700; letter-spacing: -.3px;
    text-align: right; white-space: nowrap;
  }

  /* Back */
  .card-back .info-band {
    position: absolute; left: 0; right: 0; bottom: 0; height: 172px; background: var(--paper);
  }
  .card-back .person { position: absolute; left: 34px; top: 156px; }
  .person-name { color: var(--paper); font-size: 22px; font-weight: 700; letter-spacing: .3px; }
  .person-role { color: var(--brand-blue); font-size: 13px; font-weight: 700; letter-spacing: 1px; margin-top: 2px; }

  .card-back .company {
    position: absolute; right: 32px; top: 40px; display: flex; flex-direction: column; align-items: flex-end; gap: 18px;
  }
  .company .brand-dot { width: 104px; height: 104px; margin-right: 70px; }
  .company-name { color: var(--paper); font-size: 20px; font-weight: 700; letter-spacing: .2px; white-space: nowrap; }

  .card-back .corner-mark {
    position: absolute; left: 24px; bottom: 26px; display: flex; align-items: center; gap: 10px;
  }
  .corner-mark .brand-dot { width: 64px; height: 64px; }
  .corner-mark .mark-name { color: var(--brand-blue); font-size: 17px; font-weight: 700; line-height: 1.15; }

  .card-back .contacts {
    position: absolute; left: 212px; bottom: 30px; list-style: none;
  }
  .contacts li {
    display: flex; align-items: center; gap: 10px;
    color: var(--brand-blue); font-size: 15px; font-weight: 600; line-height: 23px; letter-spacing: .3px;
    white-space: nowrap;
  }
  .contacts svg { width: 12px; height: 12px; flex: none; }

  .card-back .address {
    position: absolute; right: 30px; top: 232px; text-align: right; font-style: normal;
    color: var(--brand-blue); font-size: 14px; font-weight: 600; line-height: 19px;
  }
</style>
</head>
<body>
<main class="sheet">

  <section class="card card-front">
    <div class="flame-area" role="img" aria-label="Dark grey flame illustration rising from the lower left corner"></div>
    <div class="brand">
      <span class="brand-dot"></span>
      <span class="brand-name">Kestrel<br>Office Clearance</span>
    </div>
    <p class="web">www.kestrelofficeclearance.co.uk</p>
    <p class="tagline">FREE OFFICE CLEARANCES… YOU CANT GET BETTER THAN THAT</p>
  </section>

  <section class="card card-back">
    <div class="info-band"></div>

    <div class="company">
      <span class="brand-dot"></span>
      <span class="company-name">KESTREL OFFICE CLEARANCE</span>
    </div>

    <div class="person">
      <p class="person-name">MARK HOLLOWAY</p>
      <p class="person-role">DIRECTOR</p>
    </div>

    <div class="corner-mark">
      <span class="brand-dot"></span>
      <span class="mark-name">Kestrel</span>
    </div>

    <ul class="contacts">
      <li>
        <svg viewBox="0 0 12 12" aria-hidden="true"><rect x="3" y="0.5" width="6" height="11" rx="1.2" fill="none" stroke="#050505" stroke-width="1.2"/><circle cx="6" cy="9.5" r=".7" fill="#050505"/></svg>
        07700 153928
      </li>
      <li>
        <svg viewBox="0 0 12 12" aria-hidden="true"><path d="M2.5 1 L4.5 1 L5.3 3.6 L4 4.6 Q5 7 7.4 8 L8.4 6.7 L11 7.5 L11 9.5 Q10.5 11 9 11 Q1 10 1 2.5 Q1 1 2.5 1Z" fill="#050505"/></svg>
        01632 960418
      </li>
      <li>
        <svg viewBox="0 0 12 12" aria-hidden="true"><rect x="0.6" y="2.2" width="10.8" height="7.6" fill="none" stroke="#050505" stroke-width="1.1"/><path d="M0.8 2.5 L6 6.5 L11.2 2.5" fill="none" stroke="#050505" stroke-width="1.1"/></svg>
        mark@kestrelofficeclearance.co.uk
      </li>
      <li>
        <svg viewBox="0 0 12 12" aria-hidden="true"><circle cx="6" cy="6" r="5" fill="none" stroke="#050505" stroke-width="1.1"/><ellipse cx="6" cy="6" rx="2.2" ry="5" fill="none" stroke="#050505" stroke-width="1"/><path d="M1 6 H11" stroke="#050505" stroke-width="1"/></svg>
        www.kestrelofficeclearance.co.uk
      </li>
    </ul>

    <address class="address">
      Unit K4 B, 2-8 Fenwick Lane,<br>
      Kelmsdown,<br>
      Brackenford,<br>
      ZZ9 4QT
    </address>
  </section>

</main>
</body>
</html>
```